Business card for Luxury Portable Restroom Trailer company

We are a Luxury Portable Restroom Trailer Company Called FALCRIDGE HIRES. Based in Orange County California. We provide portable restroom trailers for events, such as, Weddings, Concerts, Charity events, Sporting events, Tournaments, Corporate events, ect. We rent and Sell the Luxury restrooms. Our colors are white, grey, and Orange. As you will see in the logo we uploaded.
There are 2 people in the company so the names and titles will change for the 3 people but card will remain the same. Here is the information for each Person: Dwight Penner CFO 555 318-0476
next Person: Leon Marchetti VP 555 318-0476
Next Person: Owen Marchetti CEO 555 318-0476
Information to include on the card: Luxury Restroom Trailers Rental and Sales. Weddings, Concerts, Charity, Sporting and Corp. Events.

```html
<!DOCTYPE html>
<html lang="en">
<head>
<meta charset="utf-8">
<title>Falcridge Hires – Business Card</title>
<link rel="stylesheet" href="https://fonts.googleapis.com/css2?family=Montserrat:wght@400;500;700;800&display=swap">
<style>
  :root {
    --orange: #f26f22;
    --white: #ffffff;
    --ink: #2b2b2b;
    --grey: #5a5a5a;
    --backdrop: #2a2a2a;
  }
  * { margin: 0; padding: 0; box-sizing: border-box; }
  html, body { width: 1200px; height: 960px; overflow: hidden; }
  body {
    background: var(--backdrop);
    font-family: "Montserrat", sans-serif;
    position: relative;
  }
  .card {
    position: absolute;
    left: 250px;
    width: 700px;
    height: 400px;
    border-radius: 22px;
    overflow: hidden;
    box-shadow: 0 14px 30px rgba(0,0,0,.45);
  }
  .card--front { top: 50px; background: var(--orange); color: var(--white); }
  .card--back { top: 510px; background: var(--white); }

  /* front */
  .front__name {
    position: absolute;
    top: 120px; left: 0; right: 0;
    text-align: center;
    font-weight: 800;
    font-size: 56px;
    letter-spacing: 3px;
    line-height: 1;
  }
  .front__services {
    position: absolute;
    top: 230px; left: 60px; right: 60px;
    text-align: center;
    font-weight: 500;
    font-size: 19px;
    line-height: 1.55;
  }
  .dot {
    display: inline-block;
    width: 9px; height: 9px;
    border-radius: 50%;
    background: var(--white);
    margin: 0 8px 2px;
    vertical-align: middle;
  }

  /* back */
  .back__swoosh { position: absolute; inset: 0; }
  .back__brand {
    position: absolute;
    left: 60px; top: 60px;
    width: 250px;
    text-align: center;
  }
  .brand-ring {
    width: 170px; height: 170px;
    margin: 0 auto 14px;
    border: 10px solid var(--orange);
    border-radius: 50%;
  }
  .brand-name {
    color: var(--orange);
    font-weight: 800;
    font-size: 22px;
    letter-spacing: 1.5px;
  }
  .back__divider {
    position: absolute;
    left: 345px; top: 40px;
    width: 2px; height: 200px;
    background: var(--orange);
  }
  .contacts {
    position: absolute;
    left: 372px; top: 30px;
    list-style: none;
  }
  .contact { margin-bottom: 10px; }
  .contact__name {
    font-weight: 800;
    font-size: 21px;
    letter-spacing: .5px;
    color: var(--grey);
    text-transform: uppercase;
    line-height: 1.1;
  }
  .contact__name span { color: var(--orange); }
  .contact__title { font-weight: 500; font-size: 15px; color: var(--ink); line-height: 1.3; }
  .contact__phone {
    display: flex; align-items: center; gap: 7px;
    font-weight: 500; font-size: 15px; color: var(--ink);
  }
  .contact__phone svg { width: 15px; height: 15px; fill: var(--orange); }
</style>
</head>
<body>

<section class="card card--front">
  <h1 class="front__name">FALCRIDGE HIRES</h1>
  <p class="front__services">
    <span class="dot"></span>Luxury Restroom Trailers Rental and Sales<br>
    <span class="dot"></span>Weddings <span class="dot"></span>Concerts <span class="dot"></span>Charity <span class="dot"></span>Sporting and Corp <span class="dot"></span>Events
  </p>
</section>

<section class="card card--back">
  <svg class="back__swoosh" viewBox="0 0 700 400" preserveAspectRatio="none" aria-hidden="true">
    <path d="M0 345 Q420 330 700 190 L700 400 L0 400 Z" fill="var(--orange)"/>
    <path d="M120 330 Q470 300 650 180 Q480 290 120 330 Z" fill="var(--grey)"/>
  </svg>

  <div class="back__brand">
    <div class="brand-ring"></div>
    <div class="brand-name">FALCRIDGE HIRES</div>
  </div>

  <div class="back__divider"></div>

  <ul class="contacts">
    <li class="contact">
      <div class="contact__name">Dwight <span>Penner</span></div>
      <div class="contact__title">CFO</div>
      <div class="contact__phone"><svg viewBox="0 0 24 24"><path d="M6.6 10.8a15.1 15.1 0 0 0 6.6 6.6l2.2-2.2a1 1 0 0 1 1-.25 11.4 11.4 0 0 0 3.6.57 1 1 0 0 1 1 1V20a1 1 0 0 1-1 1A17 17 0 0 1 3 4a1 1 0 0 1 1-1h3.5a1 1 0 0 1 1 1c0 1.25.2 2.45.57 3.57a1 1 0 0 1-.25 1z"/></svg>555 318-0476</div>
    </li>
    <li class="contact">
      <div class="contact__name">Leon <span>Marchetti</span></div>
      <div class="contact__title">VP</div>
      <div class="contact__phone"><svg viewBox="0 0 24 24"><path d="M6.6 10.8a15.1 15.1 0 0 0 6.6 6.6l2.2-2.2a1 1 0 0 1 1-.25 11.4 11.4 0 0 0 3.6.57 1 1 0 0 1 1 1V20a1 1 0 0 1-1 1A17 17 0 0 1 3 4a1 1 0 0 1 1-1h3.5a1 1 0 0 1 1 1c0 1.25.2 2.45.57 3.57a1 1 0 0 1-.25 1z"/></svg>555 318-0476</div>
    </li>
    <li class="contact">
      <div class="contact__name">Owen <span>Marchetti</span></div>
      <div class="contact__title">CEO</div>
      <div class="contact__phone"><svg viewBox="0 0 24 24"><path d="M6.6 10.8a15.1 15.1 0 0 0 6.6 6.6l2.2-2.2a1 1 0 0 1 1-.25 11.4 11.4 0 0 0 3.6.57 1 1 0 0 1 1 1V20a1 1 0 0 1-1 1A17 17 0 0 1 3 4a1 1 0 0 1 1-1h3.5a1 1 0 0 1 1 1c0 1.25.2 2.45.57 3.57a1 1 0 0 1-.25 1z"/></svg>555 318-0476</div>
    </li>
  </ul>
</section>

</body>
</html>
```